Business Card Design Project

We are a construction company in Orange County, CA. We need a two sided business card. We would like the back to be our logo with web URL. Front should included Name, title, address, phone, fax and email address.

our address is
627 West Dorrance Blvd, Suite 308
Anaheim, CA 92718

Our logo files are attached.

Construction

```html
<!DOCTYPE html>
<html lang="en">
<head>
<meta charset="utf-8">
<title>KORVEN Business Card</title>
<link rel="stylesheet" href="https://fonts.googleapis.com/css2?family=Arimo:wght@400;700&display=swap">
<style>
  :root {
    --brand-blue: #1c4d82;
    --text-blue: #2a5f96;
    --ink: #1e1e1e;
    --paper: #ffffff;
    --photo-grey: #6b6b6b;
    --stage: #e9e7e3;
  }
  * { box-sizing: border-box; margin: 0; padding: 0; }
  html, body { width: 1200px; height: 900px; overflow: hidden; }
  body {
    background: var(--stage);
    font-family: "Arimo", Arial, sans-serif;
    position: relative;
  }
  .card {
    position: absolute;
    width: 630px;
    height: 360px;
    border-radius: 22px;
    background: var(--paper);
    overflow: hidden;
    box-shadow: 0 10px 28px rgba(0,0,0,.22);
  }

  /* Back of card */
  .card--back { left: 80px; top: 60px; }
  .back-logo {
    position: absolute;
    left: 0; right: 0; top: 70px;
    text-align: center;
  }
  .back-logo__name {
    font-weight: 700;
    font-size: 104px;
    letter-spacing: -2px;
    color: var(--brand-blue);
    line-height: 1;
  }
  .back-logo__url {
    display: block;
    margin-top: 8px;
    padding-left: 120px;
    font-size: 17px;
    color: var(--brand-blue);
  }
  .back-band {
    position: absolute;
    left: 0; right: 0; bottom: 0;
    height: 92px;
    background: var(--brand-blue);
    display: flex;
    align-items: center;
    justify-content: center;
  }
  .tagline {
    color: var(--paper);
    font-size: 26px;
    letter-spacing: 7px;
    text-transform: uppercase;
  }

  /* Front of card */
  .card--front { left: 490px; top: 470px; }
  .front-band {
    position: absolute;
    left: 0; right: 0; top: 0;
    height: 128px;
    background: var(--brand-blue);
  }
  .front-logo {
    position: absolute;
    right: 34px; top: 22px;
    text-align: right;
  }
  .front-logo__name {
    font-weight: 700;
    font-size: 62px;
    letter-spacing: -1px;
    color: var(--paper);
    line-height: 1;
  }
  .front-logo__tagline {
    margin-top: 4px;
    color: var(--paper);
    font-size: 10px;
    letter-spacing: 3px;
    text-transform: uppercase;
  }
  .photo-slot {
    position: absolute;
    left: 40px; top: 62px;
    width: 120px; height: 112px;
    background: var(--photo-grey);
    border: 4px solid #ececec;
    border-radius: 6px;
    display: flex;
    align-items: center;
    justify-content: center;
    text-align: center;
    color: var(--paper);
    font-size: 20px;
    line-height: 1.2;
  }
  .identity {
    position: absolute;
    left: 172px; top: 134px;
  }
  .identity__name { color: var(--text-blue); font-size: 22px; }
  .identity__title { color: var(--ink); font-size: 10px; margin-top: 2px; }

  .contact-list {
    position: absolute;
    left: 36px; top: 202px;
    list-style: none;
  }
  .contact-list li {
    display: flex;
    align-items: center;
    gap: 18px;
    height: 31px;
    font-size: 18px;
    color: var(--ink);
    white-space: nowrap;
  }
  .contact-list svg { width: 18px; height: 18px; fill: var(--brand-blue); flex: none; }

  .address {
    position: absolute;
    right: 28px; bottom: 26px;
    text-align: right;
    font-style: normal;
    color: var(--text-blue);
    font-size: 17px;
    line-height: 1.35;
    white-space: nowrap;
  }
</style>
</head>
<body>

<section class="card card--back" aria-label="Card back">
  <div class="back-logo">
    <div class="back-logo__name">KORVEN</div>
    <span class="back-logo__url">www.yourdomain.com</span>
  </div>
  <div class="back-band">
    <p class="tagline">Plan &bull; Develop &bull; Construct</p>
  </div>
</section>

<section class="card card--front" aria-label="Card front">
  <div class="front-band"></div>
  <div class="front-logo">
    <div class="front-logo__name">KORVEN</div>
    <p class="front-logo__tagline">Plan &bull; Develop &bull; Construct</p>
  </div>

  <div class="photo-slot" role="img" aria-label="Portrait photo placeholder">Your<br>Foto</div>

  <div class="identity">
    <p class="identity__name">Darrell Whitmore</p>
    <p class="identity__title">General Manager</p>
  </div>

  <ul class="contact-list">
    <li>
      <svg viewBox="0 0 24 24" aria-hidden="true"><path d="M2 9c0-3 4-5 10-5s10 2 10 5v2h-5V9c-1-.6-3-1-5-1s-4 .4-5 1v2H2zM6 12h12l3 8H3z"/></svg>
      (00) 123-4567-890
    </li>
    <li>
      <svg viewBox="0 0 24 24" aria-hidden="true"><path d="M6 2h9v5H6zM3 8h18v13H3zm4 3v3h10v-3zm0 5v3h4v-3zm6 0v3h4v-3z"/></svg>
      (00) 123-4567-890
    </li>
    <li>
      <svg viewBox="0 0 24 24" aria-hidden="true"><path d="M2 6h20v13H2zm2 1.5 8 6 8-6z" /></svg>
      info@yourdomain.com
    </li>
    <li>
      <svg viewBox="0 0 24 24" aria-hidden="true"><path d="M12 2a10 10 0 1 0 0 20 10 10 0 0 0 0-20zm-1 2.1V7H7.6A8 8 0 0 1 11 4.1zm2 0A8 8 0 0 1 16.4 7H13zM5.3 9H11v2H4.1a8 8 0 0 1 1.2-2zM13 9h5.7a8 8 0 0 1 1.2 2H13zM4.1 13H11v2H5.3a8 8 0 0 1-1.2-2zM13 13h6.9a8 8 0 0 1-1.2 2H13zM7.6 17H11v2.9A8 8 0 0 1 7.6 17zM13 17h3.4A8 8 0 0 1 13 19.9z"/></svg>
      www.yourdomain.com
    </li>
  </ul>

  <address class="address">
    627 West Dorrance Blvd, Suite 308<br>
    Anaheim, CA 92718
  </address>
</section>

</body>
</html>
```